Exciting new vermouth brand needs a brilliant label!

We need a label design for an exciting new premium Italian Vermouth brand called Brunallo Vermouth.

Brunallo Vermouth is based on a recipe that has been handed down for four generations and is made in the traditional way in the Piedmonte region of Northern Italy.

Brunallo, which means 'heavenly' in Italian has been designed to elevate classic cocktails such as the Negroni, Americano and Manhattan with a base of Italian wine blended with botanicals such as wormwood, orange peel, rhubarb and cinchona. It has a delicately balanced bittersweet profile with hints of vanilla and citrus.

Its competitors include brands such as Doralte Mirena, Bellusi and Grevano (see the uploaded brief for more examples).

The label is for a 50cl dark bottle (please refer to the uploaded brief) and should be based on maximum dimensions of 70mm (width) x 110mm (height). There is no limit to embellishments such as foil printing, embossing or any other premium finishes. The label does not necessarily need to be rectangular.

Feedback will be given quickly and constructively after submissions to ensure that the process is as fair and useful as possible for everyone.

Target Market(s)

25-45 year old Europeans, 50:50 female:male

Industry/Entity Type

Wine / Spirits / Vermouth

Requirements
Must have
• Fantastic design that is distinct from competitors, a premium feel and great lettering.
Should not have
• Generic images or patterns that do not relate to the brand (Brunallo) or the product

```html
<!DOCTYPE html>
<html lang="en">
<head>
<meta charset="utf-8">
<title>Brunallo Vermouth – Label</title>
<link rel="stylesheet" href="https://fonts.googleapis.com/css2?family=Playfair+Display:wght@500&family=Italiana&family=Montserrat:wght@400;700&display=swap">
<style>
  :root {
    --paper: #ffffff;
    --label-black: #050403;
    --gold-deep: #8a4b12;
    --gold-mid: #c98a2a;
    --gold-light: #f8dc7c;
    --gold-pale: #fff1a6;
  }
  html, body {
    margin: 0;
    padding: 0;
    width: 1200px;
    height: 1200px;
    overflow: hidden;
    background: var(--paper);
  }
  .canvas {
    position: relative;
    width: 1200px;
    height: 1200px;
  }
  .label {
    position: absolute;
    left: 319px;
    top: 171px;
    width: 562px;
    height: 858px;
  }
  .brand-name {
    font-family: "Playfair Display", "Bodoni Moda", serif;
    font-weight: 500;
    font-size: 90px;
  }
  .product-type {
    font-family: "Italiana", "Didact Gothic", serif;
    font-size: 60px;
  }
  .tagline {
    font-family: "Montserrat", Arial, sans-serif;
    font-weight: 700;
    font-size: 17px;
    letter-spacing: 3.4px;
  }
  .descriptor, .volume {
    font-family: "Montserrat", Arial, sans-serif;
    font-weight: 400;
    font-size: 12.5px;
    letter-spacing: 0.6px;
  }
</style>
</head>
<body>
<main class="canvas">
  <svg class="label" viewBox="0 0 562 858" xmlns="http://www.w3.org/2000/svg" aria-label="Brunallo Vermouth bottle label">
    <defs>
      <linearGradient id="gold-foil" x1="0" y1="0" x2="1" y2="1">
        <stop offset="0" stop-color="var(--gold-light)"/>
        <stop offset="0.25" stop-color="var(--gold-mid)"/>
        <stop offset="0.45" stop-color="var(--gold-pale)"/>
        <stop offset="0.7" stop-color="var(--gold-deep)"/>
        <stop offset="1" stop-color="var(--gold-light)"/>
      </linearGradient>
      <linearGradient id="gold-text" x1="0" y1="0" x2="1" y2="0">
        <stop offset="0" stop-color="#e9b746"/>
        <stop offset="0.35" stop-color="var(--gold-pale)"/>
        <stop offset="0.65" stop-color="#b87420"/>
        <stop offset="1" stop-color="var(--gold-light)"/>
      </linearGradient>
      <radialGradient id="emblem-glow" cx="0.5" cy="0.45" r="0.55">
        <stop offset="0" stop-color="#d9a23c"/>
        <stop offset="0.6" stop-color="#6b3f10"/>
        <stop offset="1" stop-color="var(--label-black)"/>
      </radialGradient>
      <path id="title-arc" d="M108,232 Q281,172 454,232"/>
      <path id="sparkle" d="M0,-16 Q2,-2 16,0 Q2,2 0,16 Q-2,2 -16,0 Q-2,-2 0,-16 Z"/>
    </defs>

    <!-- outer foil border -->
    <path class="label-border" fill="url(#gold-foil)"
          d="M0,858 L0,250 Q0,110 130,62 Q281,8 432,62 Q562,110 562,250 L562,858 Z"/>
    <!-- black field -->
    <path class="label-field" fill="var(--label-black)"
          d="M30,836 L30,254 Q30,132 146,92 Q281,46 416,92 Q532,132 532,254 L532,836 Z"/>
    <!-- inner keyline -->
    <path class="label-keyline" fill="none" stroke="url(#gold-text)" stroke-width="2"
          d="M42,822 L42,258 Q42,142 152,104 Q281,60 410,104 Q520,142 520,258 L520,822 Z"/>

    <!-- top rule -->
    <line x1="190" y1="48" x2="372" y2="48" stroke="url(#gold-text)" stroke-width="4"/>

    <!-- brand name -->
    <text class="brand-name" fill="url(#gold-text)">
      <textPath href="#title-arc" startOffset="50%" text-anchor="middle" textLength="330" lengthAdjust="spacingAndGlyphs">BRUNALLO</textPath>
    </text>

    <!-- emblem area -->
    <rect class="emblem" x="120" y="268" width="322" height="234" rx="40" fill="url(#emblem-glow)"
          role="img" aria-label="Gold line illustration of a winged celestial figure"/>

    <!-- sparkles -->
    <g class="sparkles" fill="url(#gold-text)">
      <use href="#sparkle" transform="translate(281,250) scale(1.2)"/>
      <use href="#sparkle" transform="translate(145,425) scale(1.3)"/>
      <use href="#sparkle" transform="translate(394,425) scale(1.3)"/>
      <use href="#sparkle" transform="translate(218,650)"/>
      <use href="#sparkle" transform="translate(332,650)"/>
    </g>

    <!-- side rules -->
    <line x1="70" y1="314" x2="70" y2="476" stroke="url(#gold-text)" stroke-width="3"/>
    <line x1="492" y1="314" x2="492" y2="476" stroke="url(#gold-text)" stroke-width="3"/>

    <!-- product type band -->
    <rect x="52" y="502" width="458" height="118" fill="none" stroke="url(#gold-text)" stroke-width="2"/>
    <rect x="78" y="522" width="406" height="78" fill="none" stroke="url(#gold-text)" stroke-width="3"/>
    <text class="product-type" x="281" y="586" text-anchor="middle" fill="url(#gold-text)" textLength="318" lengthAdjust="spacingAndGlyphs">VERMOUTH</text>

    <!-- details panel -->
    <rect x="86" y="668" width="390" height="128" fill="none" stroke="url(#gold-text)" stroke-width="3"/>
    <path d="M96,676 L466,676 L466,788 L310,788 M252,788 L96,788 Z" fill="none" stroke="url(#gold-text)" stroke-width="1.5"/>
    <text class="tagline" x="281" y="714" text-anchor="middle" fill="url(#gold-text)">PREMIUM ITALIAN</text>
    <text class="descriptor" x="281" y="748" text-anchor="middle" fill="url(#gold-text)">WINE BLENDED</text>
    <text class="descriptor" x="281" y="766" text-anchor="middle" fill="url(#gold-text)">WITH BOTANICALS</text>
    <text class="volume" x="281" y="792" text-anchor="middle" fill="url(#gold-text)">500ML</text>

    <!-- base rule -->
    <line x1="52" y1="814" x2="510" y2="814" stroke="url(#gold-text)" stroke-width="2"/>
  </svg>
</main>
</body>
</html>
```